KDWB Business Card

Looking for a business card design to incorporate our branding. We want to only use the colors listing in the Branding Package (attached).
Updates

Target Market(s)

People who need their phone or device fixed.

Industry/Entity Type

Electronics

Contact Information for Business Card

Please use:

Brightwick Gadget Clinic LLC
4810 E Harlow Ridge Rd
Suite 417
San Antonio, TX 78163

Marcus Delgrove, Store Manager

(210) 555-0147

Requirements
Must have
• Must include the colors that are contained within the Branding Package PDF file.

```html
<!DOCTYPE html>
<html lang="en">
<head>
<meta charset="utf-8">
<title>Brightwick Gadget Clinic – Business Card</title>
<link rel="stylesheet" href="https://fonts.googleapis.com/css2?family=Open+Sans:wght@400;600;700&display=swap">
<style>
  :root {
    --brand-orange: #fe5000;
    --brand-grey: #53575a;
    --card-white: #ffffff;
    --stage: #ece9e6;
  }
  * { margin: 0; padding: 0; box-sizing: border-box; }
  html, body { width: 1200px; height: 900px; overflow: hidden; }
  body {
    background: var(--stage);
    font-family: "Open Sans", Arial, sans-serif;
    position: relative;
  }
  .card {
    position: absolute;
    overflow: hidden;
    box-shadow: 0 4px 14px rgba(0,0,0,0.18);
  }
  .card-front { left: 78px; top: 35px; width: 587px; height: 363px; background: var(--card-white); }
  .card-back  { left: 388px; top: 505px; width: 567px; height: 352px; background: var(--brand-orange); }

  .front-bands { position: absolute; left: 0; top: 0; width: 587px; height: 363px; }

  .brand-lockup {
    position: absolute; left: 0; right: 0; top: 78px;
    display: flex; align-items: center; justify-content: center; gap: 12px;
  }
  .brand-dot {
    width: 16px; height: 16px; border-radius: 50%; background: var(--brand-orange);
  }
  .brand-name {
    font-size: 34px; font-weight: 400; color: var(--brand-orange); letter-spacing: -0.5px;
  }

  .company-address {
    position: absolute; left: 29px; top: 253px;
    color: var(--card-white); font-size: 15px; line-height: 21px; font-style: normal;
  }
  .contact {
    position: absolute; right: 35px; top: 255px; text-align: right; color: var(--card-white);
  }
  .contact-name { font-size: 19px; font-weight: 700; letter-spacing: 0.3px; line-height: 26px; }
  .contact-role { font-size: 15px; line-height: 22px; margin-top: 2px; }
  .contact-phone {
    font-size: 15px; margin-top: 10px;
    display: flex; align-items: center; justify-content: flex-end; gap: 5px;
  }

  .back-lockup {
    position: absolute; inset: 0;
    display: flex; align-items: center; justify-content: center;
  }
  .back-name { font-size: 40px; font-weight: 400; color: var(--card-white); }
</style>
</head>
<body>
  <section class="card card-front">
    <svg class="front-bands" viewBox="0 0 587 363" aria-hidden="true">
      <polygon points="0,198 361,198 337,225 0,225" fill="var(--brand-grey)"/>
      <polygon points="372,190 587,190 587,363 0,363 0,228 340,228" fill="var(--brand-orange)"/>
    </svg>
    <div class="brand-lockup">
      <span class="brand-dot"></span>
      <span class="brand-name">Brightwick Gadget Clinic</span>
    </div>
    <address class="company-address">
      BRIGHTWICK GADGET CLINIC LLC<br>
      4810 E Harlow Ridge Rd<br>
      Suite 417 San Antonio<br>
      TX 78163
    </address>
    <div class="contact">
      <div class="contact-name">MARCUS DELGROVE</div>
      <div class="contact-role">Store Manager</div>
      <div class="contact-phone">(210) 555-0147
        <svg width="16" height="16" viewBox="0 0 24 24" aria-hidden="true"><path fill="#fff" d="M6.6 10.8a15.1 15.1 0 0 0 6.6 6.6l2.2-2.2c.3-.3.7-.4 1-.2 1.1.4 2.3.6 3.6.6.6 0 1 .4 1 1V20c0 .6-.4 1-1 1A17 17 0 0 1 3 4c0-.6.4-1 1-1h3.5c.6 0 1 .4 1 1 0 1.2.2 2.4.6 3.6.1.3 0 .7-.2 1z"/></svg>
      </div>
    </div>
  </section>

  <section class="card card-back">
    <div class="back-lockup">
      <span class="back-name">Brightwick</span>
    </div>
  </section>
</body>
</html>
```